MRT Property - Business Cards

Looking for a business card & general letterhead, signage etc design for our new logo.

Colours:
000a20
0056a2
00b5ef
0088ce
68cef2

Fonts:
Poppins
Karla

Please keep look and feel of new brand - example in the zip package I sent.

```html
<!DOCTYPE html>
<html lang="en">
<head>
<meta charset="utf-8">
<title>MRT Property – Business Cards</title>
<link rel="stylesheet" href="https://fonts.googleapis.com/css2?family=Poppins:wght@400;500;600;700&family=Delius&display=swap">
<style>
  :root {
    --navy: #000a20;
    --brand-blue: #0056a2;
    --card-blue: #0b58a6;
    --card-blue-deep: #084b90;
    --sky: #00b5ef;
    --mid-blue: #0088ce;
    --light-blue: #68cef2;
    --ink: #1b1b1b;
    --paper: #ffffff;
    --backdrop: #cfc8bc;
  }
  * { margin: 0; padding: 0; box-sizing: border-box; }
  html, body { width: 900px; height: 1200px; overflow: hidden; }
  body {
    background: var(--backdrop);
    font-family: "Poppins", sans-serif;
    position: relative;
  }
  .card {
    position: absolute;
    border-radius: 24px;
    overflow: hidden;
    box-shadow: 0 6px 14px rgba(0, 0, 0, 0.35);
  }
  .card-front { left: 80px; top: 131px; width: 742px; height: 440px; background: var(--paper); }
  .card-back { left: 78px; top: 638px; width: 744px; height: 440px; background: var(--card-blue); }

  /* Front */
  .brand { position: absolute; left: 76px; top: 192px; display: flex; align-items: center; gap: 14px; }
  .brand-dot { width: 52px; height: 52px; border-radius: 50%; background: var(--mid-blue); }
  .brand-name { color: var(--brand-blue); font-weight: 700; line-height: 1; }
  .brand-name .main { display: block; font-size: 54px; letter-spacing: 1px; }
  .brand-name .sub { display: block; font-size: 15px; letter-spacing: 6.5px; margin-top: 4px; padding-left: 2px; }

  .divider { position: absolute; left: 348px; top: 122px; width: 3px; height: 222px; background: var(--brand-blue); }
  .details { position: absolute; left: 365px; top: 118px; color: var(--ink); }
  .person-name { font-family: "Delius", cursive; font-size: 30px; color: var(--brand-blue); line-height: 1.2; }
  .person-title { font-size: 15px; margin-top: 2px; }
  .address { font-size: 15.5px; line-height: 21px; margin-top: 22px; }
  .contacts { list-style: none; margin-top: 22px; font-size: 15.5px; }
  .contacts li { display: flex; align-items: center; gap: 10px; height: 28px; }
  .contacts svg { width: 16px; height: 16px; fill: var(--brand-blue); flex: none; }

  /* Back */
  .back-decor {
    position: absolute; inset: 0;
    background:
      radial-gradient(ellipse 60% 80% at 10% 70%, var(--card-blue-deep), transparent 70%),
      linear-gradient(200deg, rgba(0,136,206,0.35) 0%, transparent 35%);
  }
  .back-brand { position: absolute; right: 72px; bottom: 40px; color: var(--paper); font-weight: 700; text-align: right; line-height: 1; }
  .back-brand .main { display: block; font-size: 100px; letter-spacing: 2px; }
  .back-brand .sub { display: block; font-size: 25px; letter-spacing: 9px; margin-top: 8px; margin-right: -9px; }
</style>
</head>
<body>
  <section class="card card-front">
    <div class="brand">
      <span class="brand-dot"></span>
      <span class="brand-name"><span class="main">MRT</span><span class="sub">PROPERTY</span></span>
    </div>
    <div class="divider"></div>
    <div class="details">
      <h1 class="person-name">Daniel Hart</h1>
      <p class="person-title">Managing Director</p>
      <p class="address">218 Maple Ridge Ave Suite<br>40 Dayton Ohio 45402</p>
      <ul class="contacts">
        <li><svg viewBox="0 0 24 24"><path d="M6.6 10.8a15.1 15.1 0 0 0 6.6 6.6l2.2-2.2a1 1 0 0 1 1-.25 11.4 11.4 0 0 0 3.6.57 1 1 0 0 1 1 1V20a1 1 0 0 1-1 1A17 17 0 0 1 3 4a1 1 0 0 1 1-1h3.5a1 1 0 0 1 1 1c0 1.25.2 2.45.57 3.57a1 1 0 0 1-.25 1z"/></svg>1 (555) 204-7719</li>
        <li><svg viewBox="0 0 24 24"><path d="M3 5h18v14H3z M3 5l9 7 9-7" fill="none" stroke="var(--brand-blue)" stroke-width="0"/><path d="M2 5h20v14H2zM3.5 6.5 12 12.5l8.5-6z" fill-rule="evenodd"/></svg>info@mrtproperty.com</li>
        <li><svg viewBox="0 0 24 24"><circle cx="12" cy="12" r="10"/></svg>www.mrtproperty.com</li>
      </ul>
    </div>
  </section>

  <section class="card card-back">
    <div class="back-decor" role="img" aria-label="Large faint brand symbol decoration"></div>
    <div class="back-brand"><span class="main">MRT</span><span class="sub">PROPERTY</span></div>
  </section>
</body>
</html>
```